Ecard for facebook and Instagram postings

I need 4 ecards (don't know if that is what it is called) for Facebook and Instagram postings. My Logo and company name should be incorporated and also be square. I would like to be able to insert text as I need. Examples are:

https://www.plorvexa.com/photo.php?fbid=20262841672382489&set=a.20261729249182489.516031.71298967488&type=1&relevant_count=1

https://media-a-kpt.yy.plorvexacdn.net/hpics-bmk4/2345967_657092986477056_308792573_n.jpg

I don't necessarily need images on them, just the color scheme to my business cards and the logo and business name. But if you'd like to give it an interesting look, you can go ahead and play with it. My site is tornquillmentoring.com, if you'd like to see the style of it.

Thank you!!!
Updates

I just uploaded the logo in two variations.  Thank you!

Target Market(s)

Women 16-65

Industry/Entity Type

Business

Requirements
Must have
• Logo and business name
Should not have
• No white background. I have attached business card picture so you can have an idea of what I'd like.

```html
<!DOCTYPE html>
<html lang="en">
<head>
<meta charset="utf-8">
<title>Tornquill Mentoring Services – Quote Card</title>
<link rel="stylesheet" href="https://fonts.googleapis.com/css2?family=Tinos:wght@700&family=Arimo:wght@400&display=swap">
<style>
  :root {
    --ember-dark: #2a0d02;
    --flame: #f5941e;
    --crimson: #c41a2c;
    --ink: #3a1202;
    --white: #ffffff;
    --footer: #1c0a03;
    --badge: #f07a1a;
  }
  * { margin: 0; padding: 0; box-sizing: border-box; }
  html, body { width: 1200px; height: 1200px; overflow: hidden; background: var(--ember-dark); }
  .card {
    position: relative;
    width: 1200px;
    height: 1200px;
    overflow: hidden;
    background:
      radial-gradient(ellipse 260px 700px at 760px 420px, rgba(255,140,40,0.55), transparent 70%),
      radial-gradient(ellipse 160px 760px at 520px 380px, rgba(255,120,30,0.35), transparent 70%),
      radial-gradient(ellipse 120px 700px at 980px 360px, rgba(240,110,20,0.35), transparent 70%),
      radial-gradient(ellipse 700px 220px at 980px 870px, rgba(255,200,140,0.45), transparent 70%),
      linear-gradient(90deg, #3a1403 0%, #8a3508 30%, #a8440a 55%, #d0600f 72%, #7a2a05 100%);
  }
  .top-band {
    position: absolute; left: 0; top: 0; width: 1200px; height: 20px;
    background: var(--crimson);
  }
  .quote-mark {
    position: absolute;
    font-family: 'Tinos', serif;
    font-weight: 700;
    font-size: 330px;
    line-height: 1;
  }
  .quote-mark--open { left: 58px; top: 52px; color: var(--flame); }
  .quote-mark--close { left: 945px; top: 780px; color: var(--crimson); }
  .quote-text {
    position: absolute;
    left: 50px; top: 208px; width: 1100px;
    text-align: center;
    font-family: 'Tinos', serif;
    font-weight: 700;
    font-size: 106px;
    line-height: 129px;
    color: var(--flame);
    text-shadow: 0 0 2px var(--ink), 2px 3px 4px rgba(40,10,0,0.85);
  }
  .footer {
    position: absolute; left: 0; top: 990px; width: 1200px; height: 190px;
    background: linear-gradient(180deg, rgba(28,10,3,0.55), var(--footer) 60%);
    border-top: 3px solid rgba(255,220,180,0.8);
  }
  .brand-name {
    position: absolute; left: 28px; top: 12px;
    font-family: 'Arimo', sans-serif;
    font-weight: 400;
    font-size: 92px;
    color: var(--white);
  }
  .brand-tagline {
    position: absolute; left: 32px; top: 140px;
    font-family: 'Arimo', sans-serif;
    font-size: 27px;
    letter-spacing: 6px;
    color: var(--white);
  }
  .site-url {
    position: absolute; left: 550px; top: 136px;
    font-family: 'Arimo', sans-serif;
    font-size: 34px;
    letter-spacing: 1px;
    color: var(--white);
  }
  .brand-badge {
    position: absolute; left: 1008px; top: 1011px;
    width: 144px; height: 144px;
  }
  .bottom-band {
    position: absolute; left: 0; top: 1180px; width: 1200px; height: 20px;
    background: var(--flame);
  }
</style>
</head>
<body>
  <main class="card">
    <div class="top-band"></div>
    <div class="quote-mark quote-mark--open" aria-hidden="true">&ldquo;</div>
    <p class="quote-text">Ignorance is the<br>curse of God;<br>knowledge is the<br>wing wherewith we<br>fly to heaven</p>
    <div class="quote-mark quote-mark--close" aria-hidden="true">&rdquo;</div>
    <footer class="footer">
      <div class="brand-name">Tornquill</div>
      <div class="brand-tagline">MENTORING SERVICES</div>
      <div class="site-url">tornquillmentoring.com</div>
    </footer>
    <svg class="brand-badge" viewBox="0 0 144 144" role="img" aria-label="Tornquill Mentoring Services logo mark">
      <circle cx="72" cy="72" r="66" fill="var(--badge)" stroke="var(--white)" stroke-width="8"/>
    </svg>
    <div class="bottom-band"></div>
  </main>
</body>
</html>
```